Rapid Pulse Tiny Track Karts

We are looking for a full web site for our race car category that allows us to edit and update some of the content. We would like the site to feel modern and attractive with the following features: 1. Event calender (with the ability for us to update) 2. Social media/ clip wave links 3. photo gallery (with the ability for us to update) 4. Member area with log in access (controlled access) - this area to include access to category regulations for up to 5 types of cars separately 5. Championship ladder for up to 5 different groups 6. sponsor page and sponsors scrolling across bottom of all pages. Please find attached our logo to be used and for reference on color/ style 7. page to show merchandise but no need for a store.

Industry/Entity Type

Motor racing category

Coding

Coded - Design and coding required

Number of Pages Required

5+ page

Colors
0054AA
0677BA
7BADD7
CADEEF
E8F1F8
FFF300
FFF600
FEFA6F
FFFEC7
FFFEE8
EB3D1F
EC4F4E
F09395
F8D3D4
FCEDEE

Requirements
Must have
• Ability to update calender/photo gallery/championship ladder including points/ notice board - Members section

```html
<!DOCTYPE html>
<html lang="en">
<head>
<meta charset="utf-8">
<title>Rapid Pulse Tiny Track Karts</title>
<link href="https://fonts.googleapis.com/css2?family=Bungee&family=Roboto:wght@400;500;700&display=swap" rel="stylesheet">
<style>
:root{
  --bg:#000;
  --white:#fff;
  --muted:#cfcfcf;
  --blue:#0a56d6;
  --blue-deep:#0054AA;
  --red-hot:#e8201a;
  --yellow:#FFD21A;
  --star:#f5b400;
}
*{margin:0;padding:0;box-sizing:border-box}
html,body{width:1200px;height:3803px;overflow:hidden;background:var(--bg)}
body{position:relative;font-family:"Roboto",Arial,sans-serif;color:var(--white)}
.abs{position:absolute}
.brand{font-family:"Roboto",Arial,sans-serif;font-weight:700;color:var(--white);text-transform:uppercase;text-align:center;line-height:1.15;letter-spacing:.5px}
.site-brand{left:499px;top:21px;width:202px;height:73px;border:2px solid var(--white);border-radius:8px;display:flex;align-items:center;justify-content:center;font-size:15px}
.search{left:773px;top:38px;width:231px;height:42px;border:1px solid #444;background:#0b0b0b;display:flex;align-items:center;padding-left:22px;font-size:13px;color:#999}
.search svg{position:absolute;right:14px;top:13px}
.clip-wave{left:1021px;top:42px;width:34px;height:34px;border-radius:50%;background:var(--red-hot)}
.nav{left:143px;top:118px;height:28px;display:flex;align-items:center;font-size:13.5px;text-transform:uppercase}
.nav span{margin-right:28px}
.nav .active{background:var(--yellow);color:#000;padding:6px 14px;margin-right:22px}
.nav-rule{left:143px;top:164px;width:914px;height:1px;background:#666}
.btn{position:absolute;height:34px}
.btn .face{position:absolute;left:0;top:0;bottom:0;right:26px;background:var(--red-hot);clip-path:polygon(0 0,100% 0,calc(100% - 12px) 100%,16px 100%);display:flex;align-items:center;justify-content:center;font-weight:700;font-size:15px;text-transform:uppercase;padding-left:6px}
.btn .s1,.btn .s2{position:absolute;top:0;bottom:0;width:10px;transform:skewX(28deg)}
.btn .s1{right:14px;background:var(--yellow)}
.btn .s2{right:4px;background:var(--blue)}
.hero{left:143px;top:192px;width:914px;height:462px;border:2px solid var(--white);border-radius:24px}
.hero-art{left:152px;top:201px;width:896px;height:444px;border-radius:18px;overflow:hidden;
  background:linear-gradient(115deg,#120a1e 0%,#2b1040 18%,#7a2a7e 34%,#e0671f 46%,#f0a630 52%,#8a2f8a 62%,#1c1026 78%,#0d0b12 100%)}
.hero-art::after{content:"";position:absolute;left:0;right:0;bottom:0;height:70px;background:linear-gradient(90deg,#3a1240,#7a2fa8 45%,#1fb8d8)}
.hero-panel{left:605px;top:266px;width:443px;height:313px;background:rgba(10,10,14,.85)}
.hero-title{left:682px;top:300px;font-family:"Bungee",sans-serif;font-size:50px;line-height:58px;text-transform:uppercase;font-weight:400}
.hero-title .b{color:var(--blue)}
.dots{left:582px;top:607px;display:flex;gap:10px}
.dots i{width:3px;height:8px;background:var(--white)}
.dots i.on{background:var(--yellow)}
.heading{position:absolute;left:0;width:1200px;text-align:center;font-family:"Bungee",sans-serif;font-size:52px;font-weight:400;text-transform:uppercase;line-height:1}
.heading .b{color:var(--blue)}
.under{position:absolute;left:573px;width:54px;height:9px;border-top:2px solid var(--yellow);border-bottom:2px solid var(--yellow)}
.event-img{left:143px;width:188px;height:164px}
.event-title{left:351px;font-size:14px;font-weight:500;text-transform:uppercase}
.event-text{left:351px;width:310px;font-size:11.5px;line-height:20px;color:var(--muted)}
.event-date{left:351px;font-size:11.5px;color:var(--yellow)}
.cal{left:692px;top:881px;width:366px;height:310px;border:2px solid #555}
.cal-head{left:751px;top:884px;width:256px;height:34px;background:var(--blue);display:flex;align-items:center;justify-content:center;font-size:15px;font-weight:500;text-transform:uppercase}
.cal-arrow{position:absolute;top:5px;width:24px;height:24px;border-radius:50%;background:var(--white)}
.cal-grid{left:702px;top:955px;width:346px;display:grid;grid-template-columns:repeat(7,1fr);row-gap:16px;font-size:12px;text-align:center}
.cal-grid .dh{font-weight:500;margin-bottom:6px}
.cal-grid span{line-height:20px}
.cal-grid .today{justify-self:center;width:26px;height:26px;line-height:26px;margin-top:-3px;border-radius:50%;background:var(--red-hot)}
.gal{top:1479px;width:215px;height:257px}
.gal-plus{left:472px;top:1595px;width:26px;height:26px}
.champ{top:2024px;width:170px;text-align:center}
.champ .pic{width:170px;height:170px;border-radius:50%}
.champ .name{margin-top:16px;font-size:16px;font-weight:500;text-transform:uppercase}
.champ p{margin-top:11px;font-size:12px;line-height:19px;color:var(--muted)}
.card{top:2643px;width:292px;height:349px;border:2px solid #444;padding:17px 17px 0}
.card .pic{height:211px}
.card .row{display:flex;justify-content:space-between;align-items:center;margin-top:28px;padding:0 8px}
.card .nm{font-size:17px;font-weight:500;text-transform:uppercase}
.card .pr{font-size:17px;font-weight:500;color:var(--blue)}
.card .row2{display:flex;justify-content:space-between;align-items:center;margin-top:14px;padding:0 8px}
.stars{color:var(--star);font-size:20px;letter-spacing:1px}
.shop{background:var(--red-hot);font-size:10px;font-weight:700;padding:6px 12px;text-transform:uppercase}
.arrow{position:absolute;width:40px;height:40px}
.sponsor{top:3311px;width:292px;height:113px;border:2px solid #2e2e2e;border-radius:56px;display:flex;align-items:center;justify-content:center;font-size:44px;font-weight:500;color:#3c3c3c}
.footer{left:0;top:3484px;width:1200px;height:319px}
.foot-brand{left:176px;top:3573px;width:267px;height:99px;border:2px solid var(--white);border-radius:8px;display:flex;align-items:center;justify-content:center;font-size:19px}
.foot-h{font-size:17px;font-weight:500;color:var(--yellow);text-transform:uppercase}
.contact{display:flex;align-items:center;font-size:12px}
.contact .ic{width:32px;height:32px;border-radius:50%;border:2px solid var(--white);margin-right:15px;display:flex;align-items:center;justify-content:center}
.social{left:867px;top:3612px;display:flex;gap:9px}
.social i{width:26px;height:26px;border-radius:50%}
.copy{left:0;top:3744px;width:1200px;text-align:center;font-size:12px;color:var(--muted)}
</style>
</head>
<body>

<header>
  <div class="abs site-brand brand">Rapid Pulse<br>Tiny Track Karts</div>
  <div class="abs search">Search
    <svg width="16" height="16" viewBox="0 0 16 16"><circle cx="6.5" cy="6.5" r="5" fill="none" stroke="#e8201a" stroke-width="2"/><line x1="10.5" y1="10.5" x2="15" y2="15" stroke="#e8201a" stroke-width="2"/></svg>
  </div>
  <a class="abs clip-wave" aria-label="clip wave"></a>
  <nav class="abs nav">
    <span class="active">Home</span><span>Events</span><span>Photo Gallery</span><span>Members</span><span>Championship</span><span>Sponsors</span><span>Merchandise</span>
  </nav>
  <div class="btn" style="left:933px;top:114px;width:124px"><div class="face">Login</div><i class="s1"></i><i class="s2"></i></div>
  <div class="abs nav-rule"></div>
</header>

<section class="hero-block">
  <div class="abs hero"></div>
  <div class="abs hero-art" role="img" aria-label="Neon-lit open-wheel race car speeding on a track"></div>
  <div class="abs hero-panel"></div>
  <h1 class="abs hero-title">Rapid Pulse<br><span class="b">Tiny Track</span><br>Karts</h1>
  <div class="btn" style="left:682px;top:503px;width:124px"><div class="face">Login</div><i class="s1"></i><i class="s2"></i></div>
  <div class="abs dots"><i></i><i class="on"></i><i></i></div>
</section>

<section class="events">
  <h2 class="heading" style="top:746px">Our <span class="b">Events</span></h2>
  <div class="under" style="top:816px"></div>

  <div class="abs event-img" style="top:883px;background:linear-gradient(170deg,#d8c8b0 0%,#8a7a6a 30%,#4a3a34 55%,#8a1d17 78%,#222 100%)" role="img" aria-label="Red formula car leading a race past the grandstand"></div>
  <h3 class="abs event-title" style="top:903px">Sed ut perspiciatis unde omnis iste</h3>
  <p class="abs event-text" style="top:935px">Lorem ipsum dolor sit amet, consectetur adipiscing elit, sed do eiusmod tempor incididunt ut labore et dolore magna aliqua. Ut enim ad minim veniam</p>
  <div class="abs event-date" style="top:1013px">Oct 26,2023 &nbsp;|&nbsp; Comments</div>

  <div class="abs event-img" style="top:1067px;background:linear-gradient(175deg,#2a1810 0%,#7a3418 35%,#c8542a 50%,#4a2414 70%,#120c0a 100%)" role="img" aria-label="Orange sports car racing at night with sparks"></div>
  <h3 class="abs event-title" style="top:1086px">Praising pain was born and I wilgi</h3>
  <p class="abs event-text" style="top:1118px">Lorem ipsum dolor sit amet, consectetur adipiscing elit, sed do eiusmod tempor incididunt ut labore et dolore magna aliqua. Ut enim ad minim veniam</p>
  <div class="abs event-date" style="top:1196px">Oct 26,2023 &nbsp;|&nbsp; Comments</div>

  <div class="abs cal"></div>
  <div class="abs cal-head">
    <span class="cal-arrow" style="left:12px"><svg width="24" height="24" viewBox="0 0 24 24"><path d="M17 12H7M11 8l-4 4 4 4" fill="none" stroke="#0a56d6" stroke-width="2"/></svg></span>
    October 26,2023
    <span class="cal-arrow" style="right:12px"><svg width="24" height="24" viewBox="0 0 24 24"><path d="M7 12h10M13 8l4 4-4 4" fill="none" stroke="#0a56d6" stroke-width="2"/></svg></span>
  </div>
  <div class="abs cal-grid">
    <span class="dh">MO</span><span class="dh">TUE</span><span class="dh">WED</span><span class="dh">THU</span><span class="dh">FRI</span><span class="dh">SAT</span><span class="dh">SUN</span>
    <span>31</span><span>1</span><span>2</span><span>3</span><span>4</span><span>5</span><span>6</span>
    <span>7</span><span>8</span><span>9</span><span>10</span><span>11</span><span>12</span><span>13</span>
    <span>14</span><span>15</span><span>16</span><span>17</span><span>18</span><span>19</span><span>20</span>
    <span>21</span><span>22</span><span>23</span><span>24</span><span>25</span><span class="today">26</span><span>27</span>
    <span>28</span><span>29</span><span>30</span><span>31</span><span>1</span><span>2</span><span>3</span>
  </div>
</section>

<section class="gallery">
  <h2 class="heading" style="top:1345px">Photo <span class="b">Gallery</span></h2>
  <div class="under" style="top:1416px"></div>
  <div class="abs gal" style="left:146px;background:linear-gradient(180deg,#b8782a 0%,#6a4420 35%,#3a2a1c 65%,#14100c 100%)" role="img" aria-label="Vintage miniature race car with golden bokeh"></div>
  <div class="abs gal" style="left:376px;background:linear-gradient(180deg,#1a2f6e 0%,#2f5fc4 45%,#244c9e 70%,#13285a 100%)" role="img" aria-label="Blue miniature race car model"></div>
  <svg class="abs gal-plus" viewBox="0 0 26 26"><rect x="10" y="0" width="6" height="26" fill="#fff"/><rect x="0" y="10" width="26" height="6" fill="#fff"/></svg>
  <div class="abs gal" style="left:608px;background:linear-gradient(160deg,#1a0c22 0%,#5a2a6a 30%,#b0502a 48%,#2a9ab0 62%,#3a1a4a 82%,#120a18 100%)" role="img" aria-label="Futuristic sports car with light streaks"></div>
  <div class="abs gal" style="left:838px;background:linear-gradient(180deg,#3e3833 0%,#2c2724 55%,#161412 100%)" role="img" aria-label="Black and orange open-wheel race car"></div>
  <div class="btn" style="left:520px;top:1783px;width:162px"><div class="face">Load More</div><i class="s1"></i><i class="s2"></i></div>
</section>

<section class="championship">
  <h2 class="heading" style="top:1917px">Championship</h2>
  <div class="abs champ" style="left:144px"><div class="pic" style="background:linear-gradient(180deg,#b8b8b8,#8e8e8e)" role="img" aria-label="Portrait of champion John Doe"></div><div class="name">John Doe</div><p>Sed ut perspiciatis unde omnis iste natus error sit voluptatem accus</p></div>
  <div class="abs champ" style="left:328px"><div class="pic" style="background:linear-gradient(180deg,#7a6a52,#2e4a3a)" role="img" aria-label="Portrait of champion Smitha"></div><div class="name">Smitha</div><p>Sed ut perspiciatis unde omnis iste natus error sit voluptatem accus</p></div>
  <div class="abs champ" style="left:516px"><div class="pic" style="background:linear-gradient(180deg,#d6d6d6,#8a9ab0)" role="img" aria-label="Portrait of champion Joshva"></div><div class="name">Joshva</div><p>Sed ut perspiciatis unde omnis iste natus error sit voluptatem accus</p></div>
  <div class="abs champ" style="left:700px"><div class="pic" style="background:linear-gradient(180deg,#3e4a5e,#1c2230)" role="img" aria-label="Portrait of champion Siya Doe"></div><div class="name">Siya Doe</div><p>Sed ut perspiciatis unde omnis iste natus error sit voluptatem accus</p></div>
  <div class="abs champ" style="left:886px"><div class="pic" style="background:linear-gradient(180deg,#f2f2f2,#d8d4d0)" role="img" aria-label="Portrait of champion Akitala"></div><div class="name">Akitala</div><p>Sed ut perspiciatis unde omnis iste natus error sit voluptatem accus</p></div>
  <div class="btn" style="left:520px;top:2363px;width:162px"><div class="face">View More</div><i class="s1"></i><i class="s2"></i></div>
</section>

<section class="merch">
  <h2 class="heading" style="top:2510px">Our <span class="b">Merchandise</span></h2>
  <div class="under" style="top:2581px"></div>
  <svg class="arrow" style="left:83px;top:2810px" viewBox="0 0 40 40"><circle cx="20" cy="20" r="18" fill="none" stroke="#bbb" stroke-width="2"/><path d="M28 20H12M18 14l-6 6 6 6" fill="none" stroke="#bbb" stroke-width="2"/></svg>
  <div class="abs card" style="left:142px"><div class="pic" style="background:linear-gradient(180deg,#fafafa,#e8e8e8)" role="img" aria-label="Black printed T-shirt"></div>
    <div class="row"><span class="nm">Veritatis</span><span class="pr">$56.78</span></div>
    <div class="row2"><span class="stars">★★★★★</span><span class="shop">Shop Now</span></div></div>
  <div class="abs card" style="left:453px"><div class="pic" style="background:linear-gradient(180deg,#ececec,#d6d6d6)" role="img" aria-label="Black baseball cap"></div>
    <div class="row"><span class="nm">Nemo Eni Ipsam</span><span class="pr">$56.78</span></div>
    <div class="row2"><span class="stars">★★★★★</span><span class="shop">Shop Now</span></div></div>
  <div class="abs card" style="left:765px"><div class="pic" style="background:linear-gradient(180deg,#fafafa,#ebe6df)" role="img" aria-label="Beige sneakers"></div>
    <div class="row"><span class="nm">Voluptatem</span><span class="pr">$56.78</span></div>
    <div class="row2"><span class="stars">★★★★★</span><span class="shop">Shop Now</span></div></div>
  <svg class="arrow" style="left:1077px;top:2810px" viewBox="0 0 40 40"><circle cx="20" cy="20" r="18" fill="none" stroke="#bbb" stroke-width="2"/><path d="M12 20h16M22 14l6 6-6 6" fill="none" stroke="#bbb" stroke-width="2"/></svg>
  <div class="btn" style="left:520px;top:3039px;width:162px"><div class="face">View More</div><i class="s1"></i><i class="s2"></i></div>
</section>

<section class="sponsors">
  <h2 class="heading" style="top:3170px">Our <span class="b">Sponsors</span></h2>
  <div class="under" style="top:3239px"></div>
  <svg class="arrow" style="left:83px;top:3348px" viewBox="0 0 40 40"><circle cx="20" cy="20" r="18" fill="none" stroke="#bbb" stroke-width="2"/><path d="M28 20H12M18 14l-6 6 6 6" fill="none" stroke="#bbb" stroke-width="2"/></svg>
  <div class="abs sponsor" style="left:148px">norvik</div>
  <div class="abs sponsor" style="left:455px">halden</div>
  <div class="abs sponsor" style="left:760px">quillo</div>
  <svg class="arrow" style="left:1077px;top:3348px" viewBox="0 0 40 40"><circle cx="20" cy="20" r="18" fill="none" stroke="#bbb" stroke-width="2"/><path d="M12 20h16M22 14l6 6-6 6" fill="none" stroke="#bbb" stroke-width="2"/></svg>
</section>

<footer>
  <svg class="abs footer" viewBox="0 0 1200 319" preserveAspectRatio="none">
    <polygon points="0,66 1200,7 1200,319 0,319" fill="#141414"/>
    <polygon points="18,0 30,0 12,73 0,73" fill="#FFD21A"/>
    <polygon points="38,0 56,0 38,73 20,73" fill="#e8201a"/>
    <polygon points="62,0 82,0 64,73 44,73" fill="#e8201a"/>
    <polygon points="90,0 122,0 104,73 72,73" fill="#0a56d6"/>
  </svg>
  <div class="abs foot-brand brand">Rapid Pulse<br>Tiny Track Karts</div>
  <div class="abs foot-h" style="left:524px;top:3572px">Contact Info</div>
  <div class="abs contact" style="left:526px;top:3612px"><span class="ic"><svg width="14" height="14" viewBox="0 0 24 24"><path d="M6.6 10.8a15 15 0 006.6 6.6l2.2-2.2a1 1 0 011-.25 11.4 11.4 0 003.6.6 1 1 0 011 1V20a1 1 0 01-1 1A17 17 0 013 4a1 1 0 011-1h3.5a1 1 0 011 1c0 1.25.2 2.45.6 3.6a1 1 0 01-.25 1z" fill="#fff"/></svg></span>Phone : +1 555 010 2030</div>
  <div class="abs contact" style="left:526px;top:3656px"><span class="ic"><svg width="14" height="12" viewBox="0 0 14 12"><rect x="1" y="1" width="12" height="10" fill="none" stroke="#fff" stroke-width="1.5"/><path d="M1 1l6 5 6-5" fill="none" stroke="#fff" stroke-width="1.5"/></svg></span>info@rapidpulsekarts.com</div>
  <div class="abs foot-h" style="left:865px;top:3572px">Stay Connected</div>
  <div class="abs social">
    <i style="background:#2b4fa8" aria-label="social link"></i>
    <i style="background:#e8201a" aria-label="clip wave"></i>
    <i style="background:#b88a4a" aria-label="social link"></i>
    <i style="background:#0a77c0" aria-label="social link"></i>
  </div>
  <div class="abs copy">© 2023 Rapid Pulse Tiny Track Karts .All Rights Reserved &nbsp;|&nbsp; Privacy Policy &nbsp;|&nbsp; Terms of Use</div>
</footer>

</body>
</html>
```